The Rotor Barn Ecommerce Store Banner

We need a company banner designed for the first banner in a rotating set on the main page of our E-commerce site. We sell Radio Controlled custom Quad/Hex/Octo Rotor drones (similar to SkyPod X from Falcora), as well as RC Helicopters. We also sell Radios, Electronics, batteries etc.

The banner will need to be 940x300px and the dominate RGB Color of the logo is 183,0,4. With black fonts and a small amount of grey. Looking for a banner that incorporates the primary color in the design but not overwhelmingly.

We also need the same banner in 146x44px and 292x88px for the mobile page. Their may need to be tweaks to support the size.

Lasty, 3 images that represent Fly, Control, and Focus at a size of 300x150px. These images are use as section images so that when a user goes to Fly for example all products in that category show up. There is a mouse over that uses transparent black with red highlight that has each word on the site. So the design should be almost like a silhouette that would show behind the transparent back hover over.

I have attached 3 examples that I created using regular product images. The design should not be an identifiable product but a representation of the category. Please use the attached examples as a reference and feel free to size and shape things however you like. You may also use elements from the your banner design with some tweaks to make it work.

The banner should both introduce and welcome customers to the site a promote The Rotor Barn as a great place to shop.

All of the images that I have attached as examples are to be used as a point of reference to help with the design process. None of the images are to be used in your design. Please be creative and thoughtful in your designs as the selected design will represent our store on the front page of the site.

I have attached screen captures of the Website so that you see the design of the site and the colors that are used. The Test Banner in the screen capture is just a place holder so that you can see how the banner will be positioned. None of the graphical elements in the test banner represent what we are looking for in our design.

Lastly, Please do not use the logo in your banner design.

Good Luck and I look forward to your submissions.

I have posted an update to the brief. Please have a look and take into consideration for your designs. I have also increased the contest 1st place prize from 110.00 to 175.00.

Hi Guy's,

    Just wanted to send out an update. I have made some adjustments to the requirements and have increased the budget a bit to compensate. This is the second budget increase since we have started so we are excited to see what you guys come up with.

This is the last requirements change for this project and we are looking forward to making a decision on a design soon.

Just to summarize what we have added: 
• Size additions for the banner design. Basically smaller versions of your banner for a mobile page.
• 3 simple feature images at 300x150px to be used with a transparent black hover hover. 
The total project budget is now $200.00. 

FYI, I have changed the contest to payment committed. 

For those of you that have not submitted designs I have added 2 screen captures of the website your banner and feature images will be used on to give you a point of reference. I hope that this helps.

As you know the contest ends on the 13. Please submit your designs as soon as possible to allow time for feedback.

Hi Designers,

   Just posted a quick update to the brief to further clarify what we are looking for. If you have any questions please feel free to message me. 

Thank You,
Derek M. Pollworth

Reason: Hi Designers, Thank you for your submissions to this design contest. I appreciate the effort put into your designs. Due to the level of participation in this design contest and the fact that recent invites to stimulate activity require a bit more time to submit designs I am extending this contest by 2 days. Friday at noon est in the US I expect to make a final decision on what design I move forward with. Thank You your for your understanding and participation. Derek

Target Market(s)

The target market is for both the hobbyist RC do-it-yourselfer (Build your own), media creators (Photography, Film) both hobby and professional. The market for this type of technology is mostly male.

Here is a video from one of the vendors that will be represented on the site. This is a great example of the primary audience for this site as well as the equipment and content that we are supporting.

http://vantelrig.example.nz/galleries/video/

Industry/Entity Type

Store

Font styles to use
Sans Serif

Requirements
Must have
• This is just a single banner that both introduces The Rotor Barn.com provides the customer with the feeling that we are the place that can accommodate all their Copter needs.

940x300px should be the size of the banner for the main page.
146x44px and 292x88px for the mobile page. Same banner just with tweaks to support the size.
300x150px for the feature images that represent Fly, Control, and Focus.

Try to balance the banner based on the look and feel section above.
Nice to have
• Try not to overwhelm the banner with the primary color in the logo.

I tend to like things that balances elements and makes smart use of colors. Feel free to introduce other colors if it enhances the design.

Keep the design simple yet impactful. Energetic but not overly busy.
Should not have
• A real product image from a vendor that we are carrying.

```html
<!DOCTYPE html>
<html lang="en">
<head>
<meta charset="utf-8">
<title>The Rotor Barn – Banner</title>
<link href="https://fonts.googleapis.com/css2?family=Oswald:wght@400;600&display=swap" rel="stylesheet">
<style>
  :root {
    --bg-page: #141414;
    --panel-black: #151515;
    --panel-texture: #262626;
    --brand-red: #b70004;
    --brand-red-dark: #6a0002;
    --text-light: #f2f2f2;
    --text-grey: #a4a8aa;
    --dot-grey: #8e9496;
    --dot-ring: #5a5f61;
    --porthole-frame: #22272c;
    --porthole-rim: #0b0d0f;
    --sky-top: #7fb1de;
    --sky-mid: #d3e2ee;
    --hills-far: #8fa37a;
    --hills-near: #6f8e3f;
  }
  html, body {
    margin: 0;
    padding: 0;
    width: 1200px;
    height: 383px;
    overflow: hidden;
    background: var(--bg-page);
  }
  .banner {
    position: relative;
    width: 1200px;
    height: 383px;
    overflow: hidden;
    background: radial-gradient(ellipse at 25% 45%, var(--panel-texture), var(--panel-black) 70%);
  }
  .scene {
    position: absolute;
    inset: 0;
  }
  .brand {
    position: absolute;
    left: 30px;
    top: 40px;
    display: flex;
    align-items: center;
    gap: 12px;
  }
  .brand-mark {
    width: 26px;
    height: 26px;
    background: var(--brand-red);
  }
  .brand-name {
    font-family: "Oswald", sans-serif;
    font-weight: 600;
    font-size: 32px;
    line-height: 1;
    letter-spacing: 1px;
    color: var(--text-light);
    text-transform: uppercase;
  }
  .welcome {
    position: absolute;
    left: 30px;
    top: 150px;
    width: 420px;
    font-family: "Oswald", sans-serif;
  }
  .welcome-title {
    margin: 0 0 10px;
    font-weight: 600;
    font-size: 30px;
    line-height: 1.15;
    color: var(--text-light);
    text-transform: uppercase;
  }
  .welcome-title em {
    font-style: normal;
    color: var(--brand-red);
  }
  .welcome-text {
    margin: 0;
    font-weight: 400;
    font-size: 17px;
    line-height: 1.4;
    color: var(--text-grey);
  }
  .slide-dots {
    position: absolute;
    left: 94px;
    top: 329px;
    display: flex;
    gap: 18px;
  }
  .slide-dot {
    width: 26px;
    height: 26px;
    border-radius: 50%;
    background: var(--dot-grey);
    box-shadow: inset 0 0 0 3px var(--dot-ring);
  }
  .slide-dot.is-active {
    background: var(--brand-red);
    box-shadow: inset 0 0 0 3px var(--brand-red-dark);
  }
</style>
</head>
<body>
  <div class="banner">
    <svg class="scene" width="1200" height="383" viewBox="0 0 1200 383">
      <defs>
        <linearGradient id="aerial-view" x1="0" y1="0" x2="0" y2="1">
          <stop offset="0" stop-color="var(--sky-top)"/>
          <stop offset="0.2" stop-color="var(--sky-mid)"/>
          <stop offset="0.3" stop-color="var(--hills-far)"/>
          <stop offset="1" stop-color="var(--hills-near)"/>
        </linearGradient>
      </defs>
      <rect class="porthole-frame" x="760" y="0" width="440" height="383" fill="var(--porthole-frame)"/>
      <circle class="porthole-rim" cx="760" cy="190" r="300" fill="var(--porthole-rim)"/>
      <circle class="porthole-view" cx="760" cy="190" r="272" fill="url(#aerial-view)"
              role="img" aria-label="Aerial photo through a helicopter window: a multi-camera rig over green hills and distant mountains"/>
    </svg>

    <div class="brand">
      <span class="brand-mark"></span>
      <span class="brand-name">The Rotor Barn</span>
    </div>

    <div class="welcome">
      <h1 class="welcome-title">Welcome to <em>The Rotor Barn</em></h1>
      <p class="welcome-text">Multi-rotors, helicopters, radios and parts – everything you need to build, fly and film.</p>
    </div>

    <div class="slide-dots">
      <span class="slide-dot"></span>
      <span class="slide-dot"></span>
      <span class="slide-dot is-active"></span>
    </div>
  </div>
</body>
</html>
```